QVR business card

Need a business card for a company that provides instructional design and elearning development services. The website is here: http://quorvane.studio/

I'm attaching a current logo, as well as the old business card design. While I like to keep it clean, the old design is too simplistic for my liking. The only idea I want to reuse from the old design is placing industry jargon on the back of the card, just need a better way to present it. But if you have other ideas for the back--feel free to experiment.

Please use the colors complementary to the color we have on the website. Thank you!

```html
<!DOCTYPE html>
<html lang="en">
<head>
<meta charset="utf-8">
<title>QVR business card</title>
<link rel="stylesheet" href="https://fonts.googleapis.com/css2?family=Fira+Sans:wght@400;600;700;800&family=Fira+Sans+Condensed:wght@400;500&display=swap">
<style>
  :root {
    --teal: #1eb0ae;
    --teal-dark: #168f8d;
    --gold: #c8bd8b;
    --ink: #3f4144;
    --paper: #ffffff;
    --backdrop: #ecebe8;
  }
  * { box-sizing: border-box; margin: 0; padding: 0; }
  html, body { width: 1200px; height: 935px; overflow: hidden; }
  body {
    background: var(--backdrop);
    font-family: "Fira Sans", sans-serif;
    display: flex;
    align-items: center;
    justify-content: center;
    gap: 40px;
  }
  .card {
    width: 540px;
    height: 309px;
    position: relative;
    overflow: hidden;
    box-shadow: 0 6px 18px rgba(0,0,0,0.15);
  }

  /* Front */
  .card-front { background: var(--paper); }
  .identity {
    position: absolute;
    top: 38px; left: 0; right: 0;
    text-align: center;
  }
  .brand {
    display: inline-flex;
    align-items: center;
    gap: 14px;
    color: var(--teal);
    font-weight: 700;
    font-size: 58px;
    line-height: 1;
    letter-spacing: 2px;
  }
  .brand-dot {
    width: 30px; height: 30px;
    border-radius: 50%;
    background: var(--gold);
  }
  .person-name {
    margin-top: 24px;
    color: var(--teal);
    font-weight: 700;
    font-size: 17px;
    letter-spacing: 1px;
  }
  .person-title {
    margin-top: 4px;
    color: var(--ink);
    font-size: 13px;
  }
  .contact-band {
    position: absolute;
    left: 0; right: 0; bottom: 0;
    height: 62px;
    background: var(--teal);
    border-top: 4px solid var(--gold);
    display: flex;
  }
  .contact-item {
    flex: 1;
    position: relative;
    display: flex;
    align-items: center;
    justify-content: center;
    color: var(--paper);
    font-size: 12.5px;
    padding-top: 8px;
  }
  .contact-item + .contact-item { border-left: 1px solid rgba(255,255,255,0.55); }
  .contact-icon {
    position: absolute;
    top: -14px; left: 50%;
    transform: translateX(-50%);
    width: 22px; height: 22px;
    border-radius: 50%;
    background: var(--paper);
    border: 2px solid var(--gold);
    display: flex; align-items: center; justify-content: center;
  }
  .contact-icon svg { width: 12px; height: 12px; }

  /* Back */
  .card-back {
    background: var(--teal);
    display: flex;
    align-items: center;
    padding: 0 30px;
  }
  .headline {
    color: var(--paper);
    font-weight: 800;
    font-size: 50px;
    line-height: 0.95;
    letter-spacing: 1px;
    width: 175px;
  }
  .divider {
    width: 2px;
    align-self: stretch;
    margin: 34px 22px;
    background: rgba(255,255,255,0.6);
  }
  .jargon {
    list-style: none;
    color: var(--paper);
    font-family: "Fira Sans Condensed", sans-serif;
    font-weight: 500;
    font-size: 24px;
    line-height: 1.3;
    letter-spacing: 0.5px;
  }
</style>
</head>
<body>

  <section class="card card-front">
    <div class="identity">
      <div class="brand"><span class="brand-dot"></span>QVR</div>
      <div class="person-name">MARIN DELACROIX</div>
      <div class="person-title">Managing Director</div>
    </div>
    <div class="contact-band">
      <div class="contact-item">
        <span class="contact-icon">
          <svg viewBox="0 0 24 24"><path fill="#1eb0ae" d="M6.6 10.8a15 15 0 0 0 6.6 6.6l2.2-2.2a1 1 0 0 1 1-.25 11.4 11.4 0 0 0 3.6.6 1 1 0 0 1 1 1V20a1 1 0 0 1-1 1A17 17 0 0 1 3 4a1 1 0 0 1 1-1h3.5a1 1 0 0 1 1 1c0 1.25.2 2.45.6 3.6a1 1 0 0 1-.25 1z"/></svg>
        </span>
        555-014-2273
      </div>
      <div class="contact-item">
        <span class="contact-icon">
          <svg viewBox="0 0 24 24"><rect x="2" y="5" width="20" height="14" rx="2" fill="#1eb0ae"/><path d="M3 6l9 7 9-7" fill="none" stroke="#fff" stroke-width="2"/></svg>
        </span>
        mdelacroix@quorvane.studio
      </div>
      <div class="contact-item">
        <span class="contact-icon">
          <svg viewBox="0 0 24 24" fill="none" stroke="#1eb0ae" stroke-width="2"><circle cx="12" cy="12" r="10"/><ellipse cx="12" cy="12" rx="4" ry="10"/><path d="M2 12h20"/></svg>
        </span>
        www.quorvane.studio
      </div>
    </div>
  </section>

  <section class="card card-back">
    <h2 class="headline">HOW<br>CAN<br>WE<br>HELP?</h2>
    <div class="divider"></div>
    <ul class="jargon">
      <li>MOBILE LEARNING SCORM</li>
      <li>INSTRUCTIONAL DESIGN LMS</li>
      <li>MOOCS ELEARNING HTML5</li>
      <li>ADULT LEARNING THEORY</li>
      <li>GAMIFICATION CLASSROOM</li>
      <li>XAPI BLENDED LEARNING</li>
    </ul>
  </section>

</body>
</html>
```